Brand New Product Needs Sales Focused Website Design

Looking for design of Homepage, Category Page & Product Page for single product sales focused website. TrundleCrate manufacture and distribute a brand new product to the market called PalTote-Case which is a super strong, re-useable, folding & stacking plastic box which can be seen on our current website www.paltote-case.example PalTote-Case was originally developed as an alternative to supermarket carrier bags and was pitched as a box for life against the other low end re-useable products. The original version was made from recycled plastic and pitched very much as environmental product. We are now taking a different direction and have re-designed the boxes in 5 bright and fashionable designs and although we still want the primary focus to be supermarket shopping we want to position the product as a design led, must have shopping and household accessory rather than a boring, cheap looking black plastic box. The new designs will still have the environmental benefits of being able to be re-used thousands of times and being 100% recyclable and save on the imminent 5p tax on carrier bags in the UK however the new designs will not be made from recycled material. Although the main use for PalTote-Case is supermarket shopping it has a multitude of other uses especially where you need temporary storage - laundry, back of the car, moving house/students, gardening, days out, home office filing (will take A4 file), recycling and much more - PalTote-Case is made out of super strong Polypropylene and can be easily washed and sanitised after use and can be folded and unfolded thousands of times and so will last for many years. PalTote-Case is a product that needs to be seen in action to be understood so the web design must quickly and easily communicate what PalTote-Case is and how it works - this can be done with video, images and copy. Our current website does not work for many reasons:- it is too busy, has too much information, tries too hard and ultimately isn't working. Any of the images off our current website can be supplied for use. Once the concept of the website is agreed I can get these photoshopped with the new designs. Pictures of new designs for reference will be attached to this brief. Ultimately we want the website to convert visitors to sales and therefore designers with a proven track record in this field are especially welcome to enter. We also have a Dropbox folder with over 100 product and situation images in - please send email address and we will send an invite to the folder. Due to Christmas period this competition will be run over 15 days however we may choose to extend the deadline to account for the non working days. Any questions feel free to ask - we will respond within 24 hours where possible.

```html
<!DOCTYPE html>
<html lang="en">
<head>
<meta charset="utf-8">
<title>PalTote-Case</title>
<link href="https://fonts.googleapis.com/css2?family=Open+Sans:ital,wght@0,400;0,600;0,700;1,700&display=swap" rel="stylesheet">
<style>
:root{
  --teal:#4cc7b3;
  --teal-dark:#36a592;
  --page:#5aa3a8;
  --red:#e05a5a;
  --red-dark:#c94848;
  --ink:#444;
  --muted:#666;
  --white:#fff;
  --strip:#ebeced;
}
*{box-sizing:border-box;margin:0;padding:0}
html,body{width:800px;height:1200px;overflow:hidden}
body{font-family:"Open Sans",sans-serif;background:var(--page);position:relative;color:var(--ink)}
.abs{position:absolute}
.site-header{left:0;top:0;width:800px;height:70px;background:var(--white)}
.brand{width:800px;top:20px;text-align:center;font-size:24px;font-weight:600;color:var(--teal-dark)}
.main-nav{left:0;top:70px;width:800px;height:32px;background:var(--teal);font-size:8px;color:var(--white);text-transform:uppercase}
.main-nav span{position:absolute;top:12px;transform:translateX(-50%)}
.nav-home{left:66px;top:0;width:60px;height:32px;background:var(--teal-dark)}
.nav-buy{left:638px;top:6px;width:36px;height:22px;background:var(--red)}
.hero{left:0;top:102px;width:800px;height:308px;background:radial-gradient(ellipse at 50% 40%,#9aa7ab,#6f7b86 80%)}
.hero-shadow{left:0;top:406px;width:800px;height:8px;background:linear-gradient(#2a3a40,transparent);border-radius:50%}
.slide{left:64px;top:128px;width:670px;height:251px;background:linear-gradient(100deg,#cfc4b4 0%,#b9ad9c 40%,#8c98a4 70%,#c7c0b1 100%)}
.slide-title{right:104px;top:155px;text-align:right;font-size:15px;font-weight:600;color:var(--white);line-height:23px;text-shadow:0 1px 2px rgba(0,0,0,.6)}
.slide-title em{font-style:normal;color:var(--teal)}
.dots{left:522px;top:209px}
.dots i{display:inline-block;width:8px;height:8px;border-radius:50%;background:var(--white);margin-right:3px}
.dots i:first-child{background:#2447a8}
.product{width:151px;height:196px;top:434px;background:var(--white);text-align:center}
.product-photo{height:107px}
.product-name{margin-top:14px;font-size:8.5px;color:var(--ink)}
.product-price{margin-top:5px;font-size:13px;color:var(--red)}
.btn-buy{display:inline-block;margin-top:6px;width:62px;height:22px;line-height:22px;background:var(--teal-dark);color:var(--white);font-size:7.5px;box-shadow:0 2px 0 #237a6b}
.video{left:66px;top:654px;width:258px;height:141px;background:linear-gradient(90deg,#e6e6e6 0%,#d4d4d6 60%,#9c8aa8 100%)}
.video-bar{left:66px;top:775px;width:258px;height:20px;background:#1e1e1e;color:#ddd;font-size:7px;padding:5px 0 0 70px}
.play{left:179px;top:708px}
.intro-title{left:373px;top:648px;font-size:19px;font-weight:700;color:var(--white)}
.intro-text{left:374px;top:676px;width:360px;font-size:7.5px;line-height:12px;color:var(--white)}
.bullet{left:374px;font-size:7.5px;font-style:italic;font-weight:700;color:var(--white)}
.bullet svg{vertical-align:middle;margin-right:6px}
.btn-red{background:var(--red);color:var(--white);font-size:7px;font-style:italic;font-weight:700;text-align:center;box-shadow:0 2px 0 var(--red-dark)}
.offer{left:66px;top:819px;width:668px;height:88px;background:var(--strip)}
.offer-shadow{left:100px;top:905px;width:600px;height:6px;background:linear-gradient(#2d4a50,transparent);border-radius:50%;opacity:.7}
.badge{left:76px;top:841px}
.offer-price{left:145px;top:849px;font-size:23px;color:var(--red)}
.offer-text{left:241px;top:856px;font-size:10px;color:var(--ink);white-space:nowrap}
.feature{width:153px;height:159px;top:932px;background:var(--white);text-align:center}
.feature svg{margin-top:10px}
.feature h3{margin-top:7px;font-size:8.5px;font-weight:400;color:var(--ink)}
.feature p{margin-top:6px;font-size:7px;line-height:13px;color:var(--muted);white-space:nowrap}
.btn-more{display:inline-block;margin-top:6px;width:44px;height:15px;line-height:15px;background:var(--red);color:var(--white);font-size:7px;box-shadow:0 2px 0 var(--red-dark)}
.footer-rule{left:66px;top:1119px;width:668px;height:1px;background:rgba(255,255,255,.25)}
.footer-links{left:66px;top:1136px;font-size:7.5px;color:var(--white)}
.footer-reg{left:66px;top:1155px;font-size:7.5px;color:var(--white)}
.social{left:646px;top:1138px}
.social i{display:inline-block;width:19px;height:19px;border-radius:50%;border:2px solid var(--white);margin-left:3px}
.copyright{right:66px;top:1170px;font-size:7.5px;color:var(--white)}
</style>
</head>
<body>
<header class="site-header abs">
  <div class="brand abs">PalTote-Case</div>
</header>

<nav class="main-nav abs">
  <div class="nav-home abs"></div>
  <div class="nav-buy abs"></div>
  <span style="left:96px">Home</span>
  <span style="left:211px">What do youthink?</span>
  <span style="left:353px">Plastic Pollution</span>
  <span style="left:466px">Videos</span>
  <span style="left:564px">Guarantee</span>
  <span style="left:656px">Buy</span>
  <svg class="abs" style="left:722px;top:8px" width="12" height="12" viewBox="0 0 12 12"><circle cx="5" cy="5" r="3.5" fill="none" stroke="#fff" stroke-width="1.4"/><line x1="7.6" y1="7.6" x2="11" y2="11" stroke="#fff" stroke-width="1.6"/></svg>
</nav>

<section class="hero abs"></section>
<div class="hero-shadow abs"></div>
<div class="slide abs" role="img" aria-label="Smiling woman unpacking laundry into a blue folding box beside a floral patterned box"></div>
<div class="slide-title abs">AT LAST ! A <em>SOLID FEATHERLIGHT</em> FOLDING BOXS<br>SO MANY EVERDAY PRACTICAL USES</div>
<div class="dots abs"><i></i><i></i><i></i></div>

<div class="product abs" style="left:66px">
  <div class="product-photo" role="img" aria-label="Light blue satchel style box" style="background:linear-gradient(#5b86c6,#7aa3dc)"></div>
  <div class="product-name">PERSPICIATIS UNDE OMNIS</div>
  <div class="product-price">$ 150.00</div>
  <span class="btn-buy">🛒 BUY IT</span>
</div>
<div class="product abs" style="left:238px">
  <div class="product-photo" role="img" aria-label="Wicker pattern box with name plate" style="background:linear-gradient(#5c5048,#a89478)"></div>
  <div class="product-name">PERSPICIATIS UNDE OMNIS</div>
  <div class="product-price">$ 150.00</div>
  <span class="btn-buy">🛒 BUY IT</span>
</div>
<div class="product abs" style="left:410px">
  <div class="product-photo" role="img" aria-label="Tan leather look satchel box" style="background:linear-gradient(#a45a34,#c4784c)"></div>
  <div class="product-name">PERSPICIATIS UNDE OMNIS</div>
  <div class="product-price">$ 150.00</div>
  <span class="btn-buy">🛒 BUY IT</span>
</div>
<div class="product abs" style="left:582px">
  <div class="product-photo" role="img" aria-label="Floral print box" style="background:linear-gradient(135deg,#e8dcc4,#d987a6 50%,#8fb6c8)"></div>
  <div class="product-name">PERSPICIATIS UNDE OMNIS</div>
  <div class="product-price">$ 150.00</div>
  <span class="btn-buy">🛒 BUY IT</span>
</div>

<div class="video abs" role="img" aria-label="Video still: PalTote-Case, box for life, presenter holding a box"></div>
<svg class="play abs" width="34" height="32" viewBox="0 0 34 32"><rect width="34" height="32" rx="6" fill="#c41a1a"/><path d="M12 8 L24 16 L12 24Z" fill="#fff"/></svg>
<div class="video-bar abs">0:00 / 0:00</div>

<h2 class="intro-title abs">PRAESENT VESTIBULUM</h2>
<p class="intro-text abs">Lorem ipsum dolor sit amet, consectetuipiscing elit. Prat vestibulustiecu et magnis dis parturient montes, Nascetur ridiculus mu</p>
<div class="bullet abs" style="top:717px"><svg width="10" height="10"><circle cx="5" cy="5" r="5" fill="#4cc7b3"/><path d="M4 3 L6.5 5 L4 7" stroke="#fff" fill="none"/></svg>Vero eos et accusamus et iusto odio dignissimos ducimus</div>
<div class="bullet abs" style="top:737px"><svg width="10" height="10"><circle cx="5" cy="5" r="5" fill="#4cc7b3"/><path d="M4 3 L6.5 5 L4 7" stroke="#fff" fill="none"/></svg>Denounce with righteous indignation and dislike men who are so beguiled and demoralized</div>
<div class="btn-red abs" style="left:374px;top:768px;width:82px;height:25px;line-height:25px">VIEW MORE &gt;&gt;</div>

<section class="offer abs"></section>
<div class="offer-shadow abs"></div>
<svg class="badge abs" width="52" height="52" viewBox="0 0 52 52"><circle cx="26" cy="26" r="25" fill="#d81e1e"/><text x="26" y="25" text-anchor="middle" font-family="Open Sans,sans-serif" font-weight="700" font-size="10" fill="#fff">SPECIAL</text><text x="26" y="36" text-anchor="middle" font-family="Open Sans,sans-serif" font-weight="700" font-size="10" fill="#fff">OFFER</text></svg>
<div class="offer-price abs">$14.99</div>
<div class="offer-text abs">I love PalTote-Case. It’s so light and easy to carry and holds all my shopping!</div>
<div class="btn-red abs" style="left:639px;top:850px;width:82px;height:25px;line-height:25px">BUY NOW &gt;&gt;</div>

<div class="feature abs" style="left:66px">
  <svg width="42" height="42"><circle cx="21" cy="21" r="20" fill="#36a592" stroke="#2b8a7a"/><circle cx="21" cy="20" r="7" fill="#fff"/></svg>
  <h3>WHAT DO YOU THINK?</h3>
  <p>We Really Do Want To Hear Your<br>Know What You Think &amp; Read<br>Our Reviews</p>
  <span class="btn-more">MORE</span>
</div>
<div class="feature abs" style="left:238px">
  <svg width="42" height="42"><circle cx="21" cy="21" r="20" fill="#36a592" stroke="#2b8a7a"/><path d="M14 22 h10 v5 h-10z M18 15 h10 v5 h-10z" fill="#fff"/></svg>
  <h3>PLASTIC POLLUTION</h3>
  <p>We Really Do Want To Hear Your<br>Know What You Think &amp; Read<br>Our Reviews</p>
  <span class="btn-more">MORE</span>
</div>
<div class="feature abs" style="left:409px">
  <svg width="42" height="42"><circle cx="21" cy="21" r="20" fill="#36a592" stroke="#2b8a7a"/><circle cx="21" cy="21" r="7" fill="none" stroke="#fff" stroke-width="1.5"/><rect x="20.2" y="19" width="1.6" height="6" fill="#fff"/><circle cx="21" cy="17" r="1" fill="#fff"/></svg>
  <h3>PALTOTE-CASE VIDEOS</h3>
  <p>We Really Do Want To Hear Your<br>Know What You Think &amp; Read<br>Our Reviews</p>
  <span class="btn-more">MORE</span>
</div>
<div class="feature abs" style="left:581px">
  <svg width="42" height="42"><circle cx="21" cy="21" r="20" fill="#36a592" stroke="#2b8a7a"/><path d="M14 20 h3 v8 h-3z M18 20 l3-6 c2 0 2 2 1.5 4 h5 v2 l-2 8 h-7.5z" fill="none" stroke="#fff" stroke-width="1.3"/></svg>
  <h3>LIFETIME GUARANTEE</h3>
  <p>We Really Do Want To Hear Your<br>Know What You Think &amp; Read<br>Our Reviews</p>
  <span class="btn-more">MORE</span>
</div>

<footer>
  <div class="footer-rule abs"></div>
  <div class="footer-links abs">Home &nbsp;|&nbsp; Contact Us &nbsp;|&nbsp; FAQ &nbsp;|&nbsp; Privacy Statement &nbsp;|&nbsp; Terms &amp; Conditions</div>
  <div class="footer-reg abs">Reg Design no 1800321 Patent a.p no GB1100456.7</div>
  <div class="social abs" aria-label="Social links"><i style="background:#3b5a98"></i><i style="background:#2aa3e0"></i><i style="background:#d34836"></i><i style="background:#1f7bb6"></i></div>
  <div class="copyright abs">Copyright © TrundleCrate Ltd 2013</div>
</footer>
</body>
</html>
```